Stonebrace Business Card Design

The Stonebrace Co is an aggregate (crushing) equipment dealer serving Western Canadian provinces. Stonebrace is a distributor of aggregate equipment for different manufacturers.

We are looking to change and update the existing business card which has been used since the existence of the company. A copy of existing card has been attached for reference. The Stonebrace Co logo we want to remain the same and we want the green color to remain the same.

We are wanting something new with a different look. A refreshing card to show a new modern and updated look. No longer wanting to have the manufacturers on the back of the card but something more like our logo on the back of the card with a statement like "Crushing Solutions"

ideas could be:
- card can be different colors on front and back
- front or reverse of the card could possibly be the green color with the logo in black

Target Market(s)

Owners of Aggregate/Crushing companies

Contact Information for Business Card

see above

Requirements
Must have
• - logo to remain same along with same font within logo
• - green color to remain same
Nice to have
• as noted above under project description
Should not have

```html
<!DOCTYPE html>
<html lang="en">
<head>
<meta charset="utf-8">
<title>The Stonebrace Co — Business Card</title>
<link rel="stylesheet" href="https://fonts.googleapis.com/css2?family=Arimo:wght@400;700&display=swap">
<style>
  :root {
    --brand-green: #8a8c0b;
    --ink: #1c1c1c;
    --text: #2b2b2b;
    --paper: #ffffff;
    --backdrop: #e9e7e4;
  }
  * { margin: 0; padding: 0; box-sizing: border-box; }
  html, body {
    width: 1200px; height: 900px; overflow: hidden;
    background: var(--backdrop);
    font-family: "Arimo", Arial, sans-serif;
  }
  .stage { position: relative; width: 1200px; height: 900px; }

  .card {
    position: absolute;
    background: var(--paper);
    box-shadow: 0 4px 14px rgba(0,0,0,0.12);
  }

  /* Front */
  .card-front { left: 150px; top: 80px; width: 588px; height: 363px; display: flex; }
  .brand-panel {
    width: 265px; height: 100%;
    background: var(--brand-green);
    display: flex; align-items: center; justify-content: center;
  }
  .brand-panel .brand-name {
    font-weight: 700; font-size: 26px; color: var(--ink);
    letter-spacing: 0.5px;
  }
  .contact-side { position: relative; flex: 1; padding: 68px 0 0 18px; }
  .person-name {
    font-size: 22px; font-weight: 400; color: var(--brand-green);
    letter-spacing: 0.5px; line-height: 1;
  }
  .contact-list { list-style: none; margin-top: 26px; }
  .contact-list li {
    display: flex; align-items: center; gap: 5px;
    font-size: 16px; color: var(--text); line-height: 21.5px;
  }
  .contact-list svg { width: 13px; height: 13px; fill: var(--brand-green); flex: none; }
  .address { margin-top: 21px; font-size: 16px; color: var(--text); line-height: 21.5px; font-style: normal; }
  .address strong { font-weight: 700; color: var(--ink); }

  /* Back */
  .card-back { left: 388px; top: 505px; width: 567px; height: 352px; }
  .back-mark {
    position: absolute; left: 0; right: 0; top: 118px;
    display: flex; flex-direction: column; align-items: center; gap: 22px;
  }
  .back-mark .dot { width: 54px; height: 54px; border-radius: 50%; background: var(--brand-green); }
  .back-mark .brand-name {
    font-weight: 700; font-size: 24px; color: var(--ink); letter-spacing: 0.5px;
  }
  .tagline {
    position: absolute; left: 40px; right: 39px; top: 265px;
    display: flex; align-items: center; gap: 10px;
  }
  .tagline .rule { flex: 1; height: 2px; background: var(--brand-green); }
  .tagline span {
    font-weight: 700; font-size: 15px; color: #333; letter-spacing: 0.5px;
  }
</style>
</head>
<body>
<main class="stage">

  <section class="card card-front" aria-label="Business card front">
    <div class="brand-panel">
      <span class="brand-name">Stonebrace</span>
    </div>
    <div class="contact-side">
      <h1 class="person-name">DALE MORRISON</h1>
      <ul class="contact-list">
        <li>
          <svg viewBox="0 0 16 16" aria-hidden="true"><path d="M1 6c0-2 3-3 7-3s7 1 7 3v1h-3.5V5.5h-7V7H1zM4 8h8l2 6H2zM8 9.5a2 2 0 1 0 0 4 2 2 0 0 0 0-4z"/></svg>
          780.555.0148(Direct)
        </li>
        <li>
          <svg viewBox="0 0 16 16" aria-hidden="true"><path d="M1 6c0-2 3-3 7-3s7 1 7 3v1h-3.5V5.5h-7V7H1zM4 8h8l2 6H2zM8 9.5a2 2 0 1 0 0 4 2 2 0 0 0 0-4z"/></svg>
          780.555.0192
        </li>
        <li>
          <svg viewBox="0 0 16 16" aria-hidden="true"><path d="M2 5h3V1h7l2 2v2h0v10H2zM6 2v3h6V3.5L10.5 2zM7 8v2h2V8zm3 0v2h2V8zm-3 3v2h2v-2zm3 0v2h2v-2zM3 6v8h2V6z"/></svg>
          780.555.0163
        </li>
        <li>
          <svg viewBox="0 0 16 16" aria-hidden="true"><path d="M1 3h14v10H1zm1.5 1.3V5l5.5 4 5.5-4v-.7z"/></svg>
          dale@stonebr.com
        </li>
        <li>
          <svg viewBox="0 0 16 16" aria-hidden="true"><circle cx="8" cy="8" r="7"/><path d="M5 4l3 1 1 3-2 1 1 3-3-2-1-3zM10 10l2-1 1 2-2 2z" fill="#fff"/></svg>
          www.stonebrace.ca
        </li>
      </ul>
      <address class="address">
        <strong>The Stonebrace Co.</strong><br>
        2218-48B Street<br>
        Camrose, Alberta T4V 1K3
      </address>
    </div>
  </section>

  <section class="card card-back" aria-label="Business card back">
    <div class="back-mark">
      <div class="dot" aria-hidden="true"></div>
      <div class="brand-name">THE STONEBRACE CO.</div>
    </div>
    <div class="tagline">
      <div class="rule"></div>
      <span>CRUSHING SOLUTIONS</span>
      <div class="rule"></div>
    </div>
  </section>

</main>
</body>
</html>
```